Business Cards for company that supports physicians that do medical research

Need to create a business card for Qorvel Studies (www.qorvelstudies.example), a company devoted to supporting physicians who conduct medical research. The form of the card should match the message of research and information quest. I have provided the logo of the company as an uploaded file. Designs should be simple and slick aimed at very high end clients.

Target Market(s)

Medical doctors that are also researchers

Industry/Entity Type

Medical

Contact Information for Business Card

Should feature logo and fields for personal info:
Name/title
Phone /email

Font styles to use
Serif
Sans Serif

Requirements
Must have
• Qorvel logo and fields for personal info:
• Name: Bertrand Okonfu
• Title: VP Research and Senior Analyst
• Phone: 555-203-4719
• email: info@qorvelstudies.example
Nice to have
• Interesting cards that I've seen:
• 1- all black/charcoal or very dark background
• 2- Plastic - semi-transparent
• 3- non-standard height-width ratios
• 4- Functional cards -- USB drive incorporated
Should not have
• Too busy; needs to stay very simple

```html
<!DOCTYPE html>
<html lang="en">
<head>
<meta charset="utf-8">
<title>Qorvel Studies — Business Card</title>
<link rel="stylesheet" href="https://fonts.googleapis.com/css2?family=Open+Sans:wght@400;600&display=swap">
<style>
  :root {
    --backdrop: #3b3b3b;
    --card: #f6f6f6;
    --brand-blue: #1f77c0;
    --brand-green: #3fae49;
    --ink: #474747;
    --rule: #c9c9c9;
  }
  * { margin: 0; padding: 0; box-sizing: border-box; }
  html, body {
    width: 1200px;
    height: 750px;
    overflow: hidden;
    background: var(--backdrop);
    font-family: "Open Sans", sans-serif;
  }
  .business-card {
    position: absolute;
    left: 80px;
    top: 79px;
    width: 1040px;
    height: 592px;
    background: var(--card);
    border-radius: 26px;
  }
  .brand {
    position: absolute;
    left: 107px;
    top: 268px;
    display: flex;
    align-items: center;
    gap: 16px;
  }
  .brand-dot {
    width: 22px;
    height: 22px;
    border-radius: 50%;
    background: var(--brand-green);
  }
  .brand-name {
    font-size: 44px;
    font-weight: 600;
    color: var(--brand-blue);
    line-height: 1;
    letter-spacing: -0.5px;
  }
  .divider {
    position: absolute;
    left: 533px;
    top: 193px;
    width: 2px;
    height: 212px;
    background: var(--rule);
  }
  .person {
    position: absolute;
    left: 583px;
    top: 178px;
  }
  .person-name {
    font-size: 36px;
    font-weight: 600;
    color: var(--brand-blue);
    line-height: 1.2;
  }
  .person-title {
    font-size: 26px;
    font-weight: 400;
    color: var(--brand-green);
    line-height: 1.3;
  }
  .contact-list {
    position: absolute;
    left: 583px;
    top: 290px;
    list-style: none;
  }
  .contact-item {
    display: flex;
    align-items: center;
    gap: 16px;
    height: 41.5px;
    font-size: 25px;
    color: var(--ink);
  }
  .contact-icon {
    width: 24px;
    height: 24px;
    flex: none;
    fill: var(--brand-blue);
  }
</style>
</head>
<body>
  <main class="business-card">
    <div class="brand">
      <span class="brand-dot"></span>
      <span class="brand-name">Qorvel Studies</span>
    </div>

    <div class="divider"></div>

    <div class="person">
      <h1 class="person-name">Bertrand Okonfu</h1>
      <p class="person-title">VP Research &amp; Senior Analyst</p>
    </div>

    <ul class="contact-list">
      <li class="contact-item">
        <svg class="contact-icon" viewBox="0 0 24 24" aria-hidden="true">
          <path d="M6.6 10.8c1.4 2.8 3.8 5.1 6.6 6.6l2.2-2.2c.3-.3.7-.4 1-.2 1.1.4 2.3.6 3.6.6.6 0 1 .4 1 1V20c0 .6-.4 1-1 1C10.6 21 3 13.4 3 4c0-.6.4-1 1-1h3.5c.6 0 1 .4 1 1 0 1.3.2 2.5.6 3.6.1.3 0 .7-.2 1L6.6 10.8z"/>
        </svg>
        <span>555-203-4719</span>
      </li>
      <li class="contact-item">
        <svg class="contact-icon" viewBox="0 0 24 24" aria-hidden="true">
          <path d="M2 5h20v14H2z M4 7v.4l8 5.2 8-5.2V7z" fill-rule="evenodd"/>
        </svg>
        <span>info@qorvelstudies.example</span>
      </li>
      <li class="contact-item">
        <svg class="contact-icon" viewBox="0 0 24 24" aria-hidden="true">
          <circle cx="12" cy="12" r="10"/>
          <path d="M7 6c2 1 2 3 4 3s1 3 3 3 1 3-1 5c-1-2-3-2-3-4S7 11 6 10 6 7 7 6zM15 5c1 1 3 1 3 3s-2 1-3 0 0-2 0-3z" fill="#f6f6f6"/>
        </svg>
        <span>www.qorvelstudies.example</span>
      </li>
    </ul>
  </main>
</body>
</html>
```